Expedition Cruise Sales Website for the Polar Regions (Antarctica & Arctic)

This will be a website for selling cruises.
This site should have a homepage, a ship page, destinations, and itineraries.
I have created a file specifying each page, and it is attached.
Pages:
1. Home
2. Cruise Lines
- 2.1 Ships
3. Destinations
- 3.1 Region - 3.2 Country - 3.3 City
4. Itineraries
- 4.1 Itinerary
5. Blog / Travel Tips 6. About Us
7. Contact
Please take a look on the attached pdf
Target Market(s)
Expedition Travelers
Coding
Coded - Design and coding required
Number of Pages Required
5+ page
Font styles to use
Look and feel
Each slider illustrates characteristics of the customer's brand and the style your logo design should communicate.

```html
<!DOCTYPE html>
<html lang="en">
<head>
<meta charset="utf-8">
<title>Polarvue.co – Polar Expedition Cruises</title>
<link href="https://fonts.googleapis.com/css2?family=Oswald:wght@300;400;500&family=Poppins:wght@400;500;600&display=swap" rel="stylesheet">
<style>
:root{
  --blue:#3674bd;
  --blue-dark:#1f3d72;
  --navy:#0d1a33;
  --ink:#1c2230;
  --text:#4a4f5a;
  --ice:#e8f3fb;
  --mist:#e9eef5;
  --grey:#f1f1f1;
  --white:#ffffff;
  --star:#f5a623;
}
*{box-sizing:border-box;margin:0;padding:0}
html,body{width:1200px;height:3969px;overflow:hidden}
body{position:relative;background:var(--white);font-family:"Poppins",sans-serif;color:var(--text)}
.abs{position:absolute}
.title{font-family:"Oswald",sans-serif;font-weight:300;color:var(--ink);text-transform:uppercase;font-size:60px;line-height:1;letter-spacing:.5px;display:flex;align-items:center;gap:16px}
.title .dot{width:28px;height:28px;background:var(--blue);border-radius:50%}
.oswald{font-family:"Oswald",sans-serif}
/* header */
.brand{font-family:"Poppins",sans-serif;font-weight:600;color:var(--blue);font-size:33px;display:flex;align-items:center;gap:10px}
.brand .mark{width:22px;height:22px;background:var(--blue);border-radius:4px}
.nav{left:342px;top:42px;display:flex;gap:32px;font-family:"Oswald",sans-serif;font-size:15px;color:#333;text-transform:uppercase}
.nav .active{color:var(--blue)}
/* hero */
.hero-ice{left:793px;top:92px;width:407px;height:571px;background:var(--ice)}
.hero-photo{left:0;top:148px;width:1126px;height:583px;background:linear-gradient(100deg,#2a3d55 0%,#4f7aa6 40%,#8fb2d1 70%,#5c86b0 100%)}
.hero-copy{left:74px;top:236px;color:var(--white)}
.hero-copy .small{font-family:"Oswald",sans-serif;font-weight:400;font-size:52px;line-height:1}
.hero-copy .big{font-family:"Oswald",sans-serif;font-weight:500;font-size:112px;line-height:1;letter-spacing:1px}
.hero-copy p{font-size:23px;line-height:32px;width:400px;margin-top:14px}
.btn{display:inline-block;background:var(--blue);color:var(--white);font-family:"Oswald",sans-serif;text-transform:uppercase}
.hero-btn{left:74px;top:521px;width:183px;height:52px;font-size:24px;line-height:52px;text-align:center}
.dots{left:74px;top:609px;display:flex;gap:8px}
.dots span{width:26px;height:4px;background:var(--white)}
.dots span:first-child{background:var(--blue)}
/* search */
.search{left:74px;top:656px;width:1024px;height:151px;background:var(--white);box-shadow:0 4px 14px rgba(0,0,0,.15);padding:18px 16px}
.search h3{font-family:"Oswald",sans-serif;font-weight:400;font-size:29px;color:var(--ink);text-transform:uppercase}
.fields{display:flex;gap:20px;margin-top:14px;align-items:flex-end}
.field{width:192px;border-bottom:1px solid #999;font-size:13px;color:#444;padding:0 4px 8px;display:flex;justify-content:space-between}
.search-btn{width:113px;height:35px;line-height:35px;text-align:center;background:var(--blue);color:var(--white);font-size:13px;margin-left:0}
.adv{position:absolute;right:44px;top:112px;font-size:12px;color:#333;text-decoration:underline}
/* offers */
.card-img{height:231px;width:330px}
.offer h4{font-family:"Oswald",sans-serif;font-weight:400;font-size:22px;color:var(--ink);text-transform:uppercase;margin-top:6px}
.offer p{font-size:13px;line-height:24px;color:#555;margin-top:10px;width:330px}
.offer .row{display:flex;align-items:center;gap:20px;margin-top:14px}
.price{font-family:"Oswald",sans-serif;font-size:23px;color:var(--blue)}
.more{height:42px;line-height:42px;padding:0 28px;font-size:16px}
.more.dark{background:var(--blue-dark)}
/* destinations */
.dest-band{left:0;top:1437px;width:766px;height:411px;background:var(--mist)}
.dest{overflow:hidden}
.dest .shade{position:absolute;left:0;right:0;bottom:0;height:45%;background:linear-gradient(to bottom,rgba(0,0,0,0),rgba(0,0,0,.85))}
.dest span{position:absolute;left:19px;bottom:16px;font-family:"Oswald",sans-serif;font-size:35px;line-height:37px;color:var(--white);text-transform:uppercase}
/* cruise line */
.lines-band{left:0;top:2400px;width:1200px;height:338px;background:var(--grey)}
.partner{top:2562px;width:251px;height:107px;background:var(--white);display:flex;align-items:center;justify-content:center;font-family:"Poppins",sans-serif;font-weight:600;font-size:34px;color:#9aa3ad}
.partner.on{border:1px solid #bbb;color:var(--blue-dark)}
/* testimonials */
.testi-photo{left:0;top:2906px;width:704px;height:486px;background:linear-gradient(120deg,#6a7f90 0%,#c9b79a 45%,#4d86b8 100%)}
.testi-card{left:639px;top:2977px;width:561px;height:305px;background:var(--white);padding:40px 35px}
.testi-card h5{font-family:"Oswald",sans-serif;font-weight:400;font-size:23px;color:var(--blue)}
.testi-card p{font-style:italic;font-size:14px;line-height:27px;color:#555;margin-top:12px}
.who{display:flex;align-items:center;gap:18px;margin-top:24px}
.avatar{width:70px;height:70px;border-radius:14px;background:linear-gradient(135deg,#8aa0b3,#c9b79a)}
.who .name{font-family:"Oswald",sans-serif;font-size:23px;color:var(--blue)}
.stars{color:var(--star);font-size:20px;letter-spacing:4px}
/* footer */
.footer{left:0;top:3479px;width:1200px;height:490px;background:var(--navy);color:var(--white)}
.footer h6{font-family:"Oswald",sans-serif;font-weight:400;font-size:21px;text-transform:uppercase;margin-bottom:16px}
.footer li{list-style:none;font-family:"Oswald",sans-serif;font-size:14px;line-height:38px;text-transform:uppercase;color:#dfe5ee}
.contact-row{display:flex;gap:14px;font-family:"Oswald",sans-serif;font-size:14px;line-height:23px;text-transform:uppercase;color:#dfe5ee;margin-bottom:14px}
.contact-row svg{flex:none;margin-top:4px}
.social{display:flex;gap:18px;margin-top:20px}
.social span{width:20px;height:20px;border-radius:50%;background:var(--white)}
.news p{font-family:"Oswald",sans-serif;font-size:14px;line-height:26px;text-transform:uppercase;color:#dfe5ee;width:240px}
.email{margin-top:16px;width:242px;height:46px;background:var(--white);color:#333;font-size:12px;padding:0 10px;line-height:46px;font-family:"Oswald",sans-serif;text-transform:uppercase}
.sub{margin-top:14px;width:242px;height:46px;line-height:46px;text-align:center;font-size:18px}
.copy{left:0;top:3930px;width:1200px;text-align:center;font-size:11px;color:#cfd6e0}
.foot-rule{left:0;top:3910px;width:1200px;height:1px;background:rgba(255,255,255,.15)}
</style>
</head>
<body>

<!-- header -->
<div class="abs brand" style="left:77px;top:92px"><span class="mark"></span>Polarvue.co</div>
<nav class="abs nav">
  <span class="active">Home</span><span>Cruise Lines</span><span>Destinations</span><span>Itineraries</span><span>Blog / Travel Tips</span><span>About Us</span><span>Contact Us</span>
  <svg width="14" height="14" viewBox="0 0 14 14"><rect x="2" y="5" width="10" height="8" fill="#3674bd"/><path d="M4.5 5V3.5a2.5 2.5 0 0 1 5 0V5" stroke="#3674bd" stroke-width="1.5" fill="none"/></svg>
</nav>

<!-- hero -->
<div class="abs hero-ice"></div>
<div class="abs hero-photo" role="img" aria-label="Large white cruise ship sailing through calm icy polar waters with snowy mountains"></div>
<div class="abs hero-copy">
  <div class="small">WELCOME TO</div>
  <div class="big">POLARVUE</div>
  <p>Duis aute irure dolor in reprehen derit in voluptate velit esse cillu m dolore eu fugiat.</p>
</div>
<div class="abs btn hero-btn">Book a Cruise</div>
<div class="abs dots"><span></span><span></span><span></span><span></span></div>

<section class="abs search">
  <h3>Cruise Search</h3>
  <div class="fields">
    <div class="field"><span>Destination</span><span>⬍</span></div>
    <div class="field"><span>Cruise Line</span><span>⬍</span></div>
    <div class="field"><span>Select Date</span><span>▦</span></div>
    <div class="field"><span>Price Range</span><span>⬍</span></div>
    <div class="search-btn">⌕ Search</div>
  </div>
  <span class="adv">Advanced Search</span>
</section>

<!-- featured offers -->
<h2 class="abs title" style="left:370px;top:866px">Featured Offers <span class="dot"></span></h2>
<article class="abs offer" style="left:74px;top:972px">
  <div class="card-img" role="img" aria-label="Cruise ship among Antarctic icebergs" style="background:linear-gradient(160deg,#9cc6e6,#3f8cc4)"></div>
  <h4>Best Antarctic Cruises</h4>
  <p>Excepteur sint occaecat cupidatat non proid ent, sunt in culpa qui officia deserunt mollit anim id est laborum.</p>
  <div class="row"><span class="price">$154.00</span><span class="btn more dark">More Info</span></div>
</article>
<article class="abs offer" style="left:436px;top:972px">
  <div class="card-img" role="img" aria-label="Blue and white expedition ship at sea" style="background:linear-gradient(160deg,#7fb4e0,#1e4f98)"></div>
  <h4>Top Galápagos Cruises</h4>
  <p>Excepteur sint occaecat cupidatat non proid ent, sunt in culpa qui officia deserunt mollit anim id est laborum.</p>
  <div class="row"><span class="price">$154.00</span><span class="btn more">More Info</span></div>
</article>
<article class="abs offer" style="left:797px;top:972px">
  <div class="card-img" role="img" aria-label="Cruise ship at sunset under pink clouds" style="background:linear-gradient(170deg,#e79aa6,#6a7ea8 55%,#2f5b84)"></div>
  <h4>Last-Minute Deals</h4>
  <p>Excepteur sint occaecat cupidatat non proid ent, sunt in culpa qui officia deserunt mollit anim id est laborum.</p>
  <div class="row"><span class="price">$154.00</span><span class="btn more">More Info</span></div>
</article>

<!-- destinations -->
<div class="abs dest-band"></div>
<h2 class="abs title" style="left:72px;top:1491px">Destinations <span class="dot"></span></h2>
<div class="abs dest" style="left:74px;top:1585px;width:330px;height:377px" role="img" aria-label="Cruise ship docked beside a colourful harbour town"><div style="position:absolute;inset:0;background:linear-gradient(170deg,#b8d3ea,#4d7fab)"></div><div class="shade"></div><span>Nemo Enim<br>Ipsam</span></div>
<div class="abs dest" style="left:436px;top:1585px;width:330px;height:377px" role="img" aria-label="Large cruise ship moored at a pier"><div style="position:absolute;inset:0;background:linear-gradient(170deg,#8fc0e8,#3a6c9a)"></div><div class="shade"></div><span>Nemo Enim<br>Ipsam</span></div>
<div class="abs dest" style="left:797px;top:1585px;width:330px;height:377px" role="img" aria-label="Cruise ship sailing on deep blue ocean"><div style="position:absolute;inset:0;background:linear-gradient(170deg,#c2d6e8,#1f4f82)"></div><div class="shade"></div><span>Nemo Enim<br>Ipsam</span></div>
<div class="abs dest" style="left:74px;top:1995px;width:513px;height:318px" role="img" aria-label="Cruise ship at sea under an orange sunset sky"><div style="position:absolute;inset:0;background:linear-gradient(175deg,#e6a070,#8d8ca0 50%,#2d4a6a)"></div><div class="shade"></div><span>Nemo Enim Ipsam</span></div>
<div class="abs dest" style="left:615px;top:1995px;width:513px;height:318px" role="img" aria-label="Cruise ship passing snowy mountains"><div style="position:absolute;inset:0;background:linear-gradient(175deg,#9fc3e4,#3c6d9e)"></div><div class="shade"></div><span>Nemo Enim Ipsam</span></div>

<!-- cruise lines -->
<div class="abs lines-band"></div>
<h2 class="abs title" style="left:434px;top:2465px">Cruise Line <span class="dot"></span></h2>
<svg class="abs" style="left:42px;top:2600px" width="20" height="32" viewBox="0 0 20 32"><path d="M16 2 4 16l12 14" stroke="#222" stroke-width="3" fill="none"/></svg>
<div class="abs partner" style="left:74px">Nordwake</div>
<div class="abs partner on" style="left:342px">Glacia</div>
<div class="abs partner" style="left:608px">Floeline</div>
<div class="abs partner" style="left:875px">Auroral Sea</div>
<svg class="abs" style="left:1138px;top:2600px" width="20" height="32" viewBox="0 0 20 32"><path d="M4 2l12 14L4 30" stroke="#3674bd" stroke-width="3" fill="none"/></svg>

<!-- testimonials -->
<h2 class="abs title" style="left:72px;top:2797px">Customer Testimonials <span class="dot"></span></h2>
<svg class="abs" style="left:1058px;top:2812px" width="18" height="30" viewBox="0 0 18 30"><path d="M15 2 3 15l12 13" stroke="#222" stroke-width="3" fill="none"/></svg>
<svg class="abs" style="left:1110px;top:2812px" width="18" height="30" viewBox="0 0 18 30"><path d="M3 2l12 13L3 28" stroke="#3674bd" stroke-width="3" fill="none"/></svg>
<div class="abs testi-photo" role="img" aria-label="Smiling couple on the deck of a cruise ship by the sea"></div>
<div class="abs testi-card">
  <h5>Nemo enim ipsam voluptatem quia voluptas</h5>
  <p>“ Sed ut perspiciatis unde omnis iste natus error sit voluptatem accusantium doloremque laudantium, totam rem aperiam, eaque ipsa quae ab illo inventore veritatis et quasi architecto beatae vitae dicta sunt explicabo...</p>
  <div class="who">
    <div class="avatar" role="img" aria-label="Customer portrait"></div>
    <div><div class="name">NAME HEADING</div><div class="stars">★★★★★</div></div>
  </div>
</div>

<!-- footer -->
<footer class="abs footer">
  <div class="abs brand" style="left:74px;top:232px;color:var(--blue);font-size:44px"><span class="mark" style="width:28px;height:28px"></span>Polarvue.co</div>
  <div class="abs" style="left:374px;top:58px">
    <h6>Site Map</h6>
    <ul><li>Home</li><li>Cruise Lines</li><li>Destinations</li><li>Itineraries</li><li>Blog / Travel Tips</li><li>About Us</li><li>Contact Us</li></ul>
  </div>
  <div class="abs" style="left:596px;top:58px">
    <h6>Contact Us</h6>
    <div class="contact-row"><svg width="14" height="14" viewBox="0 0 14 14"><path d="M7 1a4 4 0 0 1 4 4c0 3-4 8-4 8S3 8 3 5a4 4 0 0 1 4-4z" fill="#3674bd"/></svg><span>48 Harbor Ridge Suite 12,<br>Halden Bay 20455, Northland</span></div>
    <div class="contact-row"><svg width="14" height="14" viewBox="0 0 14 14"><path d="M3 1l3 3-2 2c1 2 2 3 4 4l2-2 3 3-2 2C6 12 2 8 1 3z" fill="#3674bd"/></svg><span>+100-555-0147</span></div>
    <div class="contact-row"><svg width="14" height="14" viewBox="0 0 14 14"><rect x="1" y="3" width="12" height="8" fill="#3674bd"/><path d="M1 3l6 5 6-5" stroke="#0d1a33" fill="none"/></svg><span>HELLO@POLARVUE.CO</span></div>
    <div class="contact-row" style="color:var(--blue);margin-top:20px"><svg width="18" height="18" viewBox="0 0 18 18"><circle cx="9" cy="9" r="7.5" stroke="#fff" stroke-width="1.5" fill="none"/></svg><span>Connect on Chat</span></div>
    <div class="social"><span></span><span></span><span></span><span></span><span></span></div>
  </div>
  <div class="abs news" style="left:884px;top:58px">
    <h6>Newsletter</h6>
    <p>Sed ut perspiciatis unde omnis iste natus error sit voluptatem</p>
    <div class="email">Enter Email Address</div>
    <div class="btn sub">Subscribe</div>
  </div>
</footer>
<div class="abs foot-rule"></div>
<div class="abs copy">Copyright © 2025 Company Name. All Rights Reserved</div>

</body>
</html>
```